Buchcover zum Thema Hausverwalter
Zielgruppe
Ich bin Autor und schreibe ein Buch über Hausverwalter.
Die Autoren sind Lorenz Waltl und Gottfried Waltl.
Der Verlag ist hollmeier & traunsteg.
Der Titel lautet: 'Mietparteien am Küchentisch - Seltsame Begebenheiten aus dem Altbau durch die Jahrzehnte'.
In diesem Buch geht es um den Beruf des Hausverwalters.
Es handelt sich um lustige Geschichten. Wir haben knapp 50 Hausverwalter aus Wien und Umgebung interviewt und von Mietern und Eigentümern die lustigsten und kuriosesten Geschichten erfahren. Es sind verrückte Sachen dabei.
Intro:
Der Hausverwalter weiß nie, was ihm der neue Arbeitstag bringen wird: überschwemmte Garagen mit schwimmenden Luxusautos, nervenaufreibende Eigentümer:innenversammlungen oder „nackerte“ Einbrecher. So unterschiedlich die Hausverwalter:innen, so unterschiedlich ihre Erinnerungen.
In seiner wechselhaften Geschichte hat der Berufsstand viel erlebt: mit Schwarzgeld gefüllte Safes oder marode Zinshäuser, oft stand er mit einem Fuß im sprichwörtlichen Kriminal. Alles vorbei. Heute stellen Dekarbonisierung und Digitalisierung den modernen und die moderne Hausverwalterin vor neue Herausforderungen.
Ich brauche ein tolles Buch Cover dafür!
Aufgabenstellung
Das Buch kommt in den österreichischen und deutschen Handel und soll ein Mega tolles Cover haben, wo Leute gerne hin greifen
So in die Richtung aber heller und freundlicher.
https://www.bildtafel-beispiel.de/pin/book-cover-design-of-the-lantern-by-the-pond--804417362950218/
https://www.bildtafel-beispiel.de/pin/47019362588204516/
https://www.bildtafel-beispiel.de/pin/629401857730415268/
https://www.bildtafel-beispiel.de/pin/317785062449138057/

```html
<!DOCTYPE html>
<html lang="de">
<head>
<meta charset="utf-8">
<title>Mietparteien am Küchentisch – Buchcover</title>
<link rel="stylesheet" href="https://fonts.googleapis.com/css2?family=Outfit:wght@500;600&family=Carlito&display=swap">
<style>
  :root {
    --backdrop: #e6e6e6;
    --backdrop-edge: #c9c9c9;
    --sky-top: #163a5a;
    --sky-mid: #1f5478;
    --tower-blue: #3cc2f0;
    --tower-steel: #5a7fa3;
    --glow-orange: #ff9a55;
    --glow-warm: #ffb27a;
    --title-ink: #ffffff;
    --band: #14232a;
    --band-ink: #eef1f3;
  }
  * { box-sizing: border-box; margin: 0; padding: 0; }
  html, body {
    width: 993px;
    height: 1200px;
    overflow: hidden;
    background: var(--backdrop);
  }
  .stage {
    position: relative;
    width: 993px;
    height: 1200px;
    border: 2px solid var(--backdrop-edge);
    background: var(--backdrop);
  }
  .cover {
    position: absolute;
    left: 195px;
    top: 123px;
    width: 603px;
    height: 954px;
    overflow: hidden;
    background: var(--sky-top);
  }
  .cover__artwork {
    position: absolute;
    inset: 0;
    background:
      radial-gradient(ellipse 14% 42% at 24% 52%, rgba(60,194,240,0.85), transparent 72%),
      radial-gradient(ellipse 10% 30% at 8% 68%, rgba(60,194,240,0.6), transparent 72%),
      radial-gradient(ellipse 12% 14% at 67% 60%, rgba(255,154,85,0.85), transparent 75%),
      radial-gradient(ellipse 18% 22% at 88% 66%, rgba(60,194,240,0.6), transparent 72%),
      radial-gradient(ellipse 45% 22% at 60% 88%, rgba(255,154,85,0.7), transparent 75%),
      radial-gradient(ellipse 30% 12% at 20% 98%, rgba(255,178,122,0.7), transparent 75%),
      linear-gradient(180deg, var(--sky-top) 0%, var(--sky-mid) 45%, var(--tower-steel) 72%, #6f86a6 88%, #8a6f78 100%);
  }
  .cover__title {
    position: absolute;
    left: 194px;
    top: 138px;
    font-family: "Outfit", sans-serif;
    font-weight: 600;
    color: var(--title-ink);
    line-height: 1;
  }
  .cover__title-line--small {
    display: block;
    font-size: 34px;
  }
  .cover__title-line--medium {
    display: block;
    font-size: 43px;
    margin-top: 2px;
  }
  .cover__title-line--large {
    display: block;
    font-size: 60px;
    margin-top: -4px;
    letter-spacing: -0.5px;
  }
  .cover__subtitle {
    position: absolute;
    left: 194px;
    top: 300px;
    width: 380px;
    font-family: "Carlito", sans-serif;
    font-size: 20px;
    line-height: 27px;
    color: var(--title-ink);
  }
  .cover__authors {
    position: absolute;
    left: 165px;
    top: 861px;
    width: 438px;
    height: 53px;
    background: var(--band);
    display: flex;
    align-items: center;
    justify-content: center;
    font-family: "Carlito", sans-serif;
    font-size: 25px;
    color: var(--band-ink);
  }
</style>
</head>
<body>
  <main class="stage">
    <section class="cover">
      <div class="cover__artwork" role="img" aria-label="Photograph of a stylised miniature city of glowing blue and orange tower blocks under a deep blue evening sky"></div>
      <h1 class="cover__title">
        <span class="cover__title-line--small">Mietparteien</span>
        <span class="cover__title-line--medium">am</span>
        <span class="cover__title-line--large">Küchentisch</span>
      </h1>
      <p class="cover__subtitle">Seltsame Begebenheiten aus dem Altbau durch die Jahrzehnte</p>
      <p class="cover__authors">Lorenz Waltl und Gottfried Waltl</p>
    </section>
  </main>
</body>
</html>
```